Brightway Haus Inc. Business Card Design

Brightway Haus Inc. is in search of a great clean design for our business cards!

Looking to incorporate our full logo and watermark on side one (however, I am open to having the text and watermark separated within the design.)

On side two, I am looking to have contact information (Name, Position, Phone #, Email, Website (www.thebrightwayhaus.ca). Can have the logo and/or watermark as part of the design if applicable.

Please add tagline "Where Shine Counts" on either side 1 or 2. This tagline can be in a sans serif, serif or cursive font as long as it compliments overall design. Capitalization can be title or sentence case depending on how it fits within the design.

Get creative!! Looking for a clean, crisp, premium design! Looking for a glossy card finish with spot UV features when printed. Cards will also be printed with rounded corners. Standard dimensions (3.5 x 2).

Target Market(s)

B2B - primary clients are business owners or property management corporations. (residential jobs are few and far between)

Industry/Entity Type

Business

Contact Information for Business Card

- clean, crisp design
- double sided
- spot UV accents and glossy finish upon printing
- standard business card size (3.5 x 2) with rounded corners
- please see project description for requirements per side

Font styles to use
Sans Serif

Requirements
Must have
• - adequate bleeds with print ready files
• - cohesive design elements between side 1 & 2
• - spot UV elements (can be on both sides or just one, use your discretion)
• - colour pallet should match the logo file provided
• - incorporate tagline "where shine counts" (this tagline can be in a serif or sans serif font as long as it is complimentary to the overall design.
Nice to have
• - Premium elements with a clean design
Should not have
• - Please omit cartoon or whimsical like designs, think premium.
• - Colours should not stray from the pallet of the provided logo.

```html
<!DOCTYPE html>
<html lang="en">
<head>
<meta charset="utf-8">
<title>Brightway Haus Inc. Business Card</title>
<link href="https://fonts.googleapis.com/css2?family=Work+Sans:wght@400;500;700;800&display=swap" rel="stylesheet">
<style>
  :root {
    --navy: #1c2557;
    --navy-deep: #161d48;
    --teal: #13b5b1;
    --white: #ffffff;
    --backdrop: #1a1a1c;
  }
  * { margin: 0; padding: 0; box-sizing: border-box; }
  html, body { width: 1200px; height: 963px; overflow: hidden; }
  body {
    background: var(--backdrop);
    font-family: "Work Sans", sans-serif;
    display: flex;
    flex-direction: column;
    align-items: center;
    justify-content: center;
    gap: 50px;
  }
  .card {
    position: relative;
    width: 700px;
    height: 400px;
    border-radius: 22px;
    overflow: hidden;
    background: linear-gradient(135deg, var(--navy) 0%, var(--navy-deep) 100%);
  }
  /* front */
  .card-front {
    display: flex;
    flex-direction: column;
    align-items: center;
    justify-content: center;
    gap: 34px;
  }
  .brand {
    display: flex;
    align-items: center;
    gap: 14px;
    font-weight: 800;
    text-transform: uppercase;
    letter-spacing: 0.5px;
    white-space: nowrap;
  }
  .brand-mark { display: block; width: 38px; height: 38px; background: var(--teal); flex: none; }
  .card-front .brand { font-size: 46px; color: var(--teal); }
  .tagline {
    color: var(--white);
    font-size: 19px;
    font-weight: 400;
    letter-spacing: 6px;
    text-transform: uppercase;
  }
  /* back */
  .back-shape { position: absolute; inset: 0; width: 700px; height: 400px; }
  .contact {
    position: absolute;
    left: 44px;
    top: 78px;
    color: var(--white);
  }
  .person { position: relative; padding-left: 22px; margin-bottom: 22px; }
  .person::before {
    content: ""; position: absolute; left: 0; top: 2px;
    width: 8px; height: 40px; background: var(--white);
  }
  .person-name { font-size: 25px; font-weight: 700; text-transform: uppercase; letter-spacing: 0.5px; line-height: 1.1; }
  .person-role { font-size: 12px; font-weight: 500; text-transform: uppercase; letter-spacing: 1.5px; margin-top: 3px; }
  .address { font-size: 15px; line-height: 1.4; margin-bottom: 12px; padding-left: 22px; }
  .details { list-style: none; font-size: 15px; line-height: 1.6; }
  .details li { display: flex; align-items: center; gap: 10px; }
  .details svg { width: 12px; height: 12px; flex: none; }
  .details .web b { font-weight: 700; }
  .card-back .brand {
    position: absolute;
    right: 44px;
    top: 92px;
    font-size: 30px;
    line-height: 1.05;
    color: var(--navy);
    gap: 12px;
  }
  .card-back .brand-mark { width: 28px; height: 28px; background: var(--navy); }
  .brand-lines { display: flex; flex-direction: column; }
</style>
</head>
<body>

  <section class="card card-front" aria-label="Card front">
    <div class="brand"><span class="brand-mark"></span>Brightway Haus Inc.</div>
    <p class="tagline">Where Shine Counts</p>
  </section>

  <section class="card card-back" aria-label="Card back">
    <svg class="back-shape" viewBox="0 0 700 400" aria-hidden="true">
      <path d="M408,0 Q275,190 505,400" fill="none" stroke="var(--teal)" stroke-width="9"/>
      <path d="M420,0 Q290,190 520,400 L700,400 L700,0 Z" fill="var(--white)"/>
    </svg>

    <div class="contact">
      <div class="person">
        <p class="person-name">Marcus Hale</p>
        <p class="person-role">Director</p>
      </div>
      <p class="address">4150 Harbor Lane Suite 210<br>Oakridge ON K2M 5R4</p>
      <ul class="details">
        <li>
          <svg viewBox="0 0 12 12"><path d="M3 1 L5 3.5 L4 5 Q5 7 7 8 L8.5 7 L11 9 L9.5 11 Q4 10.5 1 3 Z" fill="var(--white)"/></svg>
          555-014-2739
        </li>
        <li>
          <svg viewBox="0 0 12 12"><rect x="1" y="2.5" width="10" height="7" fill="none" stroke="var(--white)" stroke-width="1.3"/><path d="M1 2.5 L6 6.5 L11 2.5" fill="none" stroke="var(--white)" stroke-width="1.3"/></svg>
          info@brightwayhaus.ca
        </li>
        <li class="web">
          <svg viewBox="0 0 12 12"><circle cx="6" cy="6" r="5" fill="none" stroke="var(--white)" stroke-width="1.2"/><ellipse cx="6" cy="6" rx="2.2" ry="5" fill="none" stroke="var(--white)" stroke-width="1"/><path d="M1 6 H11" stroke="var(--white)" stroke-width="1"/></svg>
          <span>www.<b>thebrightwayhaus</b>.ca</span>
        </li>
      </ul>
    </div>

    <div class="brand"><span class="brand-mark"></span><span class="brand-lines"><span>Brightway</span><span>Haus Inc.</span></span></div>
  </section>

</body>
</html>
```